Retail Jewelry Business Card Design Project

We are in need of a new business card design for a retail jewelry store. This store is in the business of fine jewelry including but not specific to bridal jewelry, diamonds, designer jewelry and watches.

This store has been in business for 20 years but continues to strive for a modern professional appeal. The main colors use for this business are a royal blue, white and silver.

Target Market(s)

Target market is ages 18-50

Industry/Entity Type

Jewelry

Requirements
Must have
• Sales Person Name
Sales Person Email Address

Store Address
Store Phone
Website

Standard business card size. No odd shapes or sizes.
Nice to have
• Overall modern feel for card.

We have thought that a design with a nice feature of the logo on the back of the card would be nice but open to ideas.
Should not have
• No specific images of jewelry should be used.

```html
<!DOCTYPE html>
<html lang="en">
<head>
<meta charset="utf-8">
<title>Harlan Reed Fine Jewelry – Business Cards</title>
<link rel="stylesheet" href="https://fonts.googleapis.com/css2?family=Source+Sans+3:ital,wght@0,400;0,600;1,600&display=swap">
<style>
  :root {
    --royal: #2e3192;
    --lavender: #7570b3;
    --swoosh: #7b73b8;
    --white: #ffffff;
    --ink: #2b2b2b;
    --stage: #ece9e4;
  }
  * { box-sizing: border-box; margin: 0; padding: 0; }
  html, body { width: 1200px; height: 788px; overflow: hidden; }
  body {
    position: relative;
    background: var(--stage);
    font-family: "Source Sans 3", "Myriad Pro", Arial, sans-serif;
    color: var(--ink);
  }
  .side-label {
    position: absolute;
    width: 525px;
    text-align: center;
    font-size: 22px;
    color: #222;
  }
  .card {
    position: absolute;
    width: 525px;
    height: 300px;
    border-radius: 22px;
    overflow: hidden;
    background: var(--white);
  }
  .card--front { left: 55px; top: 73px; }
  .card--back-white { left: 621px; top: 73px; }
  .card--back-royal { left: 54px; top: 446px; background: var(--royal); }
  .card--back-lavender { left: 621px; top: 446px; background: var(--lavender); }

  .front-wave { position: absolute; inset: 0; width: 525px; height: 300px; }

  .brand-name {
    font-weight: 600;
    color: var(--royal);
    text-align: center;
    line-height: 1.05;
  }
  .front-brand {
    position: absolute;
    left: 20px; top: 90px;
    width: 235px;
    font-size: 30px;
  }
  .front-divider {
    position: absolute;
    left: 263px; top: 77px;
    width: 1px; height: 90px;
    background: #555;
  }
  .contact {
    position: absolute;
    left: 278px; top: 76px;
    font-size: 13.5px;
    line-height: 24px;
    color: #333;
  }
  .contact__name {
    font-size: 17px;
    color: var(--royal);
    line-height: 26px;
    margin-bottom: 2px;
  }
  .contact__key { font-weight: 600; font-style: italic; }
  .front-address {
    position: absolute;
    left: 0; right: 0; top: 270px;
    text-align: center;
    font-size: 13px;
    color: var(--white);
  }

  .back-brand {
    position: absolute;
    left: 0; right: 0; top: 78px;
    font-size: 50px;
  }
  .back-web {
    position: absolute;
    left: 0; right: 0; top: 259px;
    text-align: center;
    font-size: 13px;
    letter-spacing: 2px;
  }
  .card--back-white .back-web { color: var(--royal); }
  .card--back-royal .brand-name,
  .card--back-royal .back-web { color: var(--white); }
  .card--back-lavender .back-web { color: #1e1e2e; }
</style>
</head>
<body>
  <div class="side-label" style="left:55px; top:32px;">Front</div>
  <div class="side-label" style="left:621px; top:32px;">Back - 1</div>
  <div class="side-label" style="left:54px; top:403px;">Back - 2</div>
  <div class="side-label" style="left:621px; top:403px;">Back - 3</div>

  <section class="card card--front">
    <svg class="front-wave" viewBox="0 0 525 300" aria-hidden="true">
      <path d="M340,250 C440,244 505,205 525,150 L525,178 C500,228 440,250 345,252 Z" fill="var(--swoosh)"/>
      <path d="M0,268 C110,228 250,238 345,255 C435,268 500,230 525,190 L525,300 L0,300 Z" fill="var(--royal)"/>
    </svg>
    <div class="brand-name front-brand">Harlan Reed<br>Fine Jewelry</div>
    <div class="front-divider"></div>
    <div class="contact">
      <div class="contact__name">Harlan Reed Calloway</div>
      <div><span class="contact__key">p</span> : 555-014-2290</div>
      <div><span class="contact__key">e</span> : harlan@harlanreedjewelry.com</div>
      <div><span class="contact__key">w</span> : www.harlanreedjewelry.com</div>
    </div>
    <div class="front-address">2280 Marlow Avenue, Bayport, FL 32999</div>
  </section>

  <section class="card card--back-white">
    <div class="brand-name back-brand">Harlan Reed<br>Fine Jewelry</div>
    <div class="back-web">www.harlanreedjewelry.com</div>
  </section>

  <section class="card card--back-royal">
    <div class="brand-name back-brand">Harlan Reed<br>Fine Jewelry</div>
    <div class="back-web">www.harlanreedjewelry.com</div>
  </section>

  <section class="card card--back-lavender">
    <div class="brand-name back-brand">Harlan Reed<br>Fine Jewelry</div>
    <div class="back-web">www.harlanreedjewelry.com</div>
  </section>
</body>
</html>
```